Letter and Envelope Design For Harborline Realty

Please design a letter and an envelope incorporating our logo (See Attached). We are also launched a business card contest. Since we want them to match, please feel free to submit a design for both the business card and also the letter design and envelope.

Requirements
Must have
• The envelope, the letter and the business cards must match somehow connecting the designs. We want them to have something that holds them together besides the logo.

```html
<!DOCTYPE html>
<html lang="en">
<head>
<meta charset="utf-8">
<title>Harborline Realty – Letterhead and Envelope</title>
<link href="https://fonts.googleapis.com/css2?family=Montserrat:wght@600&family=Source+Sans+3:wght@400;600&display=swap" rel="stylesheet">
<style>
  :root{
    --brand-blue:#0b1c8f;
    --band-grey:#4b4b4b;
    --paper:#f8f8f8;
    --backdrop:#e6e6e6;
    --ink:#3a3a3a;
    --ink-dark:#2b2b2b;
    --white:#ffffff;
  }
  *{margin:0;padding:0;box-sizing:border-box}
  html,body{width:1200px;height:825px;overflow:hidden;background:var(--backdrop)}
  .canvas{position:relative;width:1200px;height:825px;font-family:"Source Sans 3",Arial,sans-serif;color:var(--ink)}
  .sheet{position:absolute;background:var(--paper);overflow:hidden}
  .letterhead{left:80px;top:86px;width:461px;height:651px}
  .envelope-front{left:591px;top:251px;width:529px;height:230px}
  .envelope-back{left:591px;top:507px;width:529px;height:230px}

  .brand{position:absolute;display:flex;flex-direction:column;align-items:center;width:120px}
  .brand-circle{width:44px;height:44px;border:2px solid var(--brand-blue);border-radius:50%}
  .brand-name{margin-top:6px;font-family:"Montserrat",Arial,sans-serif;font-weight:600;color:var(--brand-blue);
    font-size:11.5px;letter-spacing:1.6px;line-height:13px;text-align:center;text-transform:uppercase}
  .letterhead .brand{left:52px;top:21px}
  .envelope-front .brand{left:26px;top:17px}

  .salutation{position:absolute;left:34px;top:149px;font-weight:600;font-size:11.5px;color:var(--ink-dark)}
  .letter-body{position:absolute;left:34px;top:175px;width:391px;font-size:9.6px;line-height:12px;text-align:justify}
  .letter-body p{margin-bottom:12px}
  .signature{position:absolute;left:36px;top:502px;width:84px;height:40px;border-radius:4px;
    background:linear-gradient(90deg,#ececec,#e2e2e2)}

  .contact-band{position:absolute;left:0;bottom:0;width:100%;height:17px}
  .contact-band svg{position:absolute;inset:0}
  .contact-line{position:absolute;top:0;height:17px;display:flex;align-items:center;gap:7px;
    font-size:7.2px;color:var(--white);white-space:nowrap}
  .contact-line span{display:flex;align-items:center;gap:2px}
  .contact-line svg{position:static;width:7px;height:7px}
  .web{position:absolute;top:0;height:17px;display:flex;align-items:center;font-size:7.4px;letter-spacing:.6px;color:var(--white)}
  .letterhead .contact-line{left:27px}
  .letterhead .web{left:341px}
  .envelope-front .contact-line{left:34px}
  .envelope-front .web{left:410px}

  .flap{position:absolute;left:0;top:0;width:529px;height:70px}
  .flap-name{position:absolute;left:0;width:100%;top:24px;text-align:center;font-family:"Montserrat",Arial,sans-serif;
    font-weight:600;font-size:9px;letter-spacing:1.4px;color:var(--white)}
</style>
</head>
<body>
<main class="canvas">

  <section class="sheet letterhead" aria-label="Letterhead">
    <div class="brand">
      <div class="brand-circle"></div>
      <div class="brand-name">Harborline<br>Realty</div>
    </div>

    <p class="salutation">Dear Mr. Dalton,</p>
    <div class="letter-body">
      <p>Lorem Ipsum is simply dummy text of the printing and typesetting industry. Lorem Ipsum has been the industry's standard dummy text ever since the 1500s, when an unknown printer took a galley of type and scrambled it to make a type specimen book. It has survived not only five centuries, but also the leap into electronic typesetting, remaining essentially unchanged.</p>
      <p>The standard chunk of Lorem Ipsum used since the 1500s is reproduced below for those interested. Sections 1.10.32 and 1.10.33 from "de Finibus Bonorum et Malorum" by Ottavian Pell are also reproduced in their exact original form, accompanied by English versions from the 1914 translation by H. Marlow</p>
      <p>Lorem Ipsum is simply dummy text of the printing and typesetting industry. Lorem Ipsum has been the industry's standard dummy text ever since the 1500s, when an unknown printer took a galley of type and scrambled it to make a type specimen book. It has survived not only five centuries, but also the leap into electronic typesetting, remaining essentially unchanged. It was popularised in the</p>
      <p>Lorem Ipsum is simply dummy text of the printing and typesetting industry. Lorem Ipsum has been the industry's standard dummy text ever since the 1500s, when an unknown printer took a galley of type and scrambled it to make a type specimen book. It has survived not only five centuries, but also the leap into electronic typesetting, remaining essentially unchanged. It was popularised in the</p>
      <p>Lorem Ipsum is simply dummy text of the printing and typesetting industry. Lorem Ipsum has been the industry's standard dummy text ever since the 1500s, when an unknown printer took a galley of type and scrambled it to make a type specimen book.</p>
    </div>
    <div class="signature" role="img" aria-label="Handwritten signature of the sender"></div>

    <div class="contact-band">
      <svg width="461" height="17" viewBox="0 0 461 17" aria-hidden="true">
        <rect width="461" height="17" fill="var(--brand-blue)"/>
        <polygon points="334,0 438,0 445,8.5 438,17 334,17 341,8.5" fill="var(--band-grey)"/>
        <polyline points="331,0 338,8.5 331,17" fill="none" stroke="var(--white)" stroke-width="1.2"/>
        <polyline points="442,0 449,8.5 442,17" fill="none" stroke="var(--white)" stroke-width="1.2"/>
      </svg>
      <div class="contact-line">
        <span><svg viewBox="0 0 10 10"><path d="M2 1l2 2-1 1.5c.6 1.2 1.3 1.9 2.5 2.5L7 6l2 2-1.5 1.5C4 9 1 6 .5 2.5z" fill="#fff"/></svg>555-014-2290</span>
        <span><svg viewBox="0 0 10 10"><rect x="1" y="2.5" width="8" height="5.5" fill="#fff"/><polyline points="1,2.5 5,6 9,2.5" fill="none" stroke="var(--brand-blue)" stroke-width="1"/></svg>info@harborline.com</span>
        <span><svg viewBox="0 0 10 10"><path d="M5 .5a3 3 0 0 1 3 3c0 2.3-3 6-3 6s-3-3.7-3-6a3 3 0 0 1 3-3z" fill="#fff"/><circle cx="5" cy="3.5" r="1.1" fill="var(--brand-blue)"/></svg>Po. box 201, Street Name, City Name, Zip Code - 00000</span>
      </div>
      <div class="web">www.harborline.com</div>
    </div>
  </section>

  <section class="sheet envelope-front" aria-label="Envelope front">
    <div class="brand">
      <div class="brand-circle"></div>
      <div class="brand-name">Harborline<br>Realty</div>
    </div>
    <div class="contact-band">
      <svg width="529" height="17" viewBox="0 0 529 17" aria-hidden="true">
        <rect width="529" height="17" fill="var(--brand-blue)"/>
        <polygon points="404,0 504,0 511,8.5 504,17 404,17 411,8.5" fill="var(--band-grey)"/>
        <polyline points="401,0 408,8.5 401,17" fill="none" stroke="var(--white)" stroke-width="1.2"/>
        <polyline points="508,0 515,8.5 508,17" fill="none" stroke="var(--white)" stroke-width="1.2"/>
      </svg>
      <div class="contact-line">
        <span><svg viewBox="0 0 10 10"><path d="M2 1l2 2-1 1.5c.6 1.2 1.3 1.9 2.5 2.5L7 6l2 2-1.5 1.5C4 9 1 6 .5 2.5z" fill="#fff"/></svg>555-014-2290</span>
        <span><svg viewBox="0 0 10 10"><rect x="1" y="2.5" width="8" height="5.5" fill="#fff"/><polyline points="1,2.5 5,6 9,2.5" fill="none" stroke="var(--brand-blue)" stroke-width="1"/></svg>info@harborline.com</span>
        <span><svg viewBox="0 0 10 10"><path d="M5 .5a3 3 0 0 1 3 3c0 2.3-3 6-3 6s-3-3.7-3-6a3 3 0 0 1 3-3z" fill="#fff"/><circle cx="5" cy="3.5" r="1.1" fill="var(--brand-blue)"/></svg>Po. box 201, Street Name, City Name, Zip Code - 00000</span>
      </div>
      <div class="web">www.harborline.com</div>
    </div>
  </section>

  <section class="sheet envelope-back" aria-label="Envelope back">
    <svg class="flap" viewBox="0 0 529 70" aria-hidden="true">
      <path d="M0 0 H529 L523 20 Q518 30 490 34 L300 64 Q264 71 228 64 L40 34 Q12 30 7 20 Z" fill="var(--brand-blue)"/>
    </svg>
    <div class="flap-name">HARBORLINE REALTY</div>
  </section>

</main>
</body>
</html>
```